Visitenkarten und Briefpapier
Zielgruppe
Planung und Realisierung von individuellen und wertbeständigen Kamin- und Ofenlösungen, sowie Fliesen- und Baddesign.
Aufgabenstellung
Wir benötigen ein möglichst schlichtes Design für Visitenkarten, bzw. Briefpapier. Für die Visitenkarten gerne auch Vorschläge mit Prägung, Ausstanzung oder mit Heißfolie. Auch Klappkarten wären denkbar. Das Design soll "das gewisse Etwas haben" und nicht zu verspielt sein.
Die Visitenkarten sind für die Firma KORVA, das Logo von der Ausstellung "raumfunke" soll dezent mit eingebunden werden (bei dem Briefpapier z.B. in der Fußzeile". Die farbliche Gestaltung sollte sich an den Farben des Logos orientieren.
Schriftart für Texte: Century Gothic
Schriftfarbe: RAL 7016
Nur eine Idee: Ich könnte mir auch gut vorstellen, dass die Visitenkarte aus einer Zündholzverpackung (wenn dann aber eine besondere mit nur einem Zündholz oder einem besonders breiten) besteht: http://glimmvelo.de/produkte_briefchen.php

```html
<!DOCTYPE html>
<html lang="de">
<head>
<meta charset="utf-8">
<title>KORVA Visitenkarte</title>
<link rel="stylesheet" href="https://fonts.googleapis.com/css2?family=Didact+Gothic&family=Questrial&display=swap">
<style>
  :root {
    --backdrop: #c09a5e;
    --paper: #ffffff;
    --anthracite: #172426;
    --ink: #1c2426;
    --flame: #f57a0a;
    --light: #f2f2f2;
  }
  html, body {
    margin: 0;
    padding: 0;
    overflow: hidden;
  }
  .canvas {
    position: relative;
    width: 1200px;
    height: 1120px;
    background: var(--backdrop);
    overflow: hidden;
    font-family: "Didact Gothic", "Questrial", sans-serif;
  }
  .card {
    position: absolute;
    left: 271px;
    width: 602px;
    height: 389px;
    overflow: hidden;
  }
  .card--front { top: 112px; background: var(--paper); }
  .card--back { top: 570px; background: var(--anthracite); }

  .brand {
    position: absolute;
    left: 18px;
    top: 22px;
  }
  .brand__name {
    margin: 0;
    font-family: "Questrial", sans-serif;
    font-size: 64px;
    line-height: 1;
    letter-spacing: 3px;
    color: var(--ink);
  }
  .brand__tagline {
    margin: 8px 0 0;
    font-size: 20px;
    color: var(--ink);
    letter-spacing: 0.3px;
  }

  .person {
    position: absolute;
    left: 0;
    right: 0;
    top: 174px;
    text-align: center;
  }
  .person__name {
    margin: 0;
    font-family: "Questrial", sans-serif;
    font-size: 35px;
    font-weight: 400;
    line-height: 1;
    color: var(--ink);
    letter-spacing: 0.5px;
  }
  .person__role {
    margin: 1px 0 0;
    font-size: 13px;
    color: var(--flame);
  }

  .contact-band {
    position: absolute;
    left: 0;
    right: 0;
    top: 253px;
    bottom: 0;
    background: var(--anthracite);
    color: var(--light);
  }
  .address {
    position: absolute;
    left: 18px;
    top: 8px;
    margin: 0;
    font-style: normal;
    font-family: "Questrial", sans-serif;
    font-size: 19px;
    line-height: 24px;
    letter-spacing: 2px;
  }
  .phones {
    position: absolute;
    left: 18px;
    top: 62px;
    margin: 0;
    font-size: 17px;
    line-height: 21px;
    letter-spacing: 0.5px;
  }
  .phones span { display: inline-block; width: 49px; }
  .web-line {
    position: absolute;
    left: 18px;
    right: 10px;
    bottom: 8px;
    display: flex;
    justify-content: space-between;
    font-size: 15px;
    letter-spacing: 1.6px;
  }

  .back-mark {
    position: absolute;
    left: 0;
    right: 0;
    top: 150px;
    margin: 0;
    text-align: center;
    font-family: "Questrial", sans-serif;
    font-size: 80px;
    line-height: 1;
    letter-spacing: 6px;
    color: var(--flame);
  }
  .exhibition {
    position: absolute;
    right: 16px;
    bottom: 16px;
    text-align: right;
    color: var(--light);
  }
  .exhibition__name {
    margin: 0;
    font-family: "Questrial", sans-serif;
    font-size: 20px;
    line-height: 1;
  }
  .exhibition__claim {
    margin: 2px 0 0;
    font-size: 6px;
    letter-spacing: 0.5px;
  }
</style>
</head>
<body>
<div class="canvas">

  <section class="card card--front">
    <header class="brand">
      <h1 class="brand__name">KORVA</h1>
      <p class="brand__tagline">kamine · öfen · fliesen</p>
    </header>

    <div class="person">
      <h2 class="person__name">Lennart Korva</h2>
      <p class="person__role">Geschäftsführer</p>
    </div>

    <div class="contact-band">
      <address class="address">Am Lindenhang 12a<br>35612&nbsp;&nbsp;&nbsp;Wendau</address>
      <p class="phones"><span>fon:</span>05714 / 38 91 40<br><span>fax:</span>05714 / 38 91 48</p>
      <div class="web-line">
        <span>info@korva-wendau.de</span>
        <span>www.korva-wendau.de</span>
      </div>
    </div>
  </section>

  <section class="card card--back">
    <p class="back-mark">KORVA</p>
    <div class="exhibition">
      <p class="exhibition__name">raumfunke</p>
      <p class="exhibition__claim">feuer raum garten</p>
    </div>
  </section>

</div>
</body>
</html>
```